4D Cradle Glimpse Luxury Ultrasound Billboard

Design a HIGH-END, MODERN billboard for my private prenatal ultrasound studio, 4D Cradle Glimpse, located in Pace, Florida.
This billboard will be viewed by drivers traveling at highway speeds, so it must be extremely clean, simple, and readable within 6 seconds.
About My Business
4D Cradle Glimpse is a private prenatal ultrasound studio specializing in:
Highest technology 4D/HD Ultrasounds
Early Gender Determination
Pregnancy Confirmation
I have been serving families for nearly 10 years and is known for creating a memorable experience, not just an ultrasound appointment.
Design Style
I DO NOT want:
Flowers
Leaves
Swirls
Glitter
Hearts everywhere
Busy backgrounds
Generic maternity stock graphics
I DO want:
Modern
Luxury
Upscale
Clean
Professional
Eye-catching
Premium medical spa feel
Colors
Use colors from my logo:
LOGO Green ( or a deep green)
Black
White
Soft Gold accents
Images:
Incorporate my professional headshot in a clean, modern way, logo, and the ultrasound images
Text
Keep wording minimal.
Primary Headline ( OPEN TO IDEAS) :
EXAMPLES ( WOULD RATHER SOMETHING MORE CATCHY)
" ADVANCED IMAGING. UNFORGETTABLE MOMENTS"
"MEET YOUR BABY BEFORE BIRTH"
Under headline:
4D Ultrasound • Early Gender • Pregnancy Confirmation
Business Name:
4D Cradle Glimpse
Private Prenatal Ultrasound Studio
Phone Number:
850-471-5923
Important
This billboard must be readable in 5–6 seconds from a moving vehicle.
Less text is better.
The phone number and business name must be visible from a distance.
The design should feel like a premium brand that immediately tells expecting parents:
“This is where I go to see my baby.”
Files Provided
Official logo
Headshot
Ultrasound images
Don’t make this look like a medical office billboard.
Make it look like a luxury baby experience billboard. That’s what separates 4D Cradle Glimpse from hospitals, OB offices, and all the new studios popping up around you. The emotional connection is what gets moms to book. ❤️
Billboard Size - 10.6” x 36”

```html
<!DOCTYPE html>
<html lang="en">
<head>
<meta charset="utf-8">
<title>4D Cradle Glimpse Billboard</title>
<link href="https://fonts.googleapis.com/css2?family=Archivo+Black&family=Kaushan+Script&family=Poppins:wght@600;700;800&display=swap" rel="stylesheet">
<style>
  :root {
    --stage: #7b838c;
    --paper: #ffffff;
    --green: #2f4a40;
    --green-ink: #1f3a30;
    --gold: #d49a2b;
    --frame-grey: #8a8f8c;
    --scan-warm: #b85a2e;
    --scan-dark: #2a1208;
    --portrait-green: #3d5a4a;
  }
  * { box-sizing: border-box; margin: 0; padding: 0; }
  html, body { width: 1145px; height: 1200px; overflow: hidden; }
  body { background: var(--stage); position: relative; }

  .billboard {
    position: absolute;
    left: 32px; top: 441px;
    width: 1080px; height: 318px;
    background: var(--paper);
    overflow: hidden;
    box-shadow: 0 10px 24px rgba(0,0,0,.35);
  }
  .billboard__bands { position: absolute; inset: 0; }

  .portrait {
    position: absolute; left: 0; top: 0;
    width: 278px; height: 318px;
    background: linear-gradient(180deg, #f4efe8 0%, #e6dccf 35%, var(--portrait-green) 75%, #2c3d34 100%);
  }

  .corner { position: absolute; border-color: var(--gold); border-style: solid; }
  .corner--top { left: 204px; top: 7px; width: 45px; height: 40px; border-width: 3px 0 0 3px; }
  .corner--bottom { left: 800px; top: 112px; width: 40px; height: 38px; border-width: 0 3px 3px 0; }

  .headline {
    position: absolute; left: 226px; top: 12px; width: 624px;
    font-family: "Archivo Black", sans-serif;
    font-size: 50px; line-height: 1;
    color: var(--green-ink);
    text-align: center;
    white-space: nowrap;
  }
  .tagline {
    position: absolute; left: 250px; top: 68px; width: 576px;
    font-family: "Kaushan Script", cursive;
    font-size: 54px; line-height: 1.1;
    color: var(--gold);
    text-align: center;
    white-space: nowrap;
  }
  .services {
    position: absolute; left: 284px; top: 146px;
    width: 510px; height: 28px;
    background: var(--green);
    border-radius: 8px;
    color: var(--paper);
    font-family: "Poppins", sans-serif;
    font-weight: 700; font-size: 15px;
    display: flex; align-items: center; justify-content: center; gap: 10px;
    white-space: nowrap;
  }

  .studio-card {
    position: absolute; left: 445px; top: 190px;
    width: 236px; height: 118px;
    background: var(--paper);
    border: 2px solid var(--frame-grey);
    border-radius: 12px;
    display: flex; flex-direction: column; align-items: center; justify-content: center; gap: 8px;
  }
  .studio-card__name {
    font-family: "Poppins", sans-serif;
    font-weight: 800; font-size: 20px;
    color: var(--gold);
    white-space: nowrap;
  }
  .studio-card__rule { width: 200px; height: 1px; background: var(--gold); }
  .studio-card__line {
    font-family: "Poppins", sans-serif;
    font-weight: 600; font-size: 9px; letter-spacing: 0.4px;
    color: var(--green);
    white-space: nowrap;
  }

  .phone {
    position: absolute; left: 697px; top: 252px;
    display: flex; align-items: center; gap: 8px;
  }
  .phone__icon {
    width: 34px; height: 34px; border-radius: 50%;
    background: var(--gold);
    display: flex; align-items: center; justify-content: center;
    flex: none;
  }
  .phone__number {
    font-family: "Poppins", sans-serif;
    font-weight: 800; font-size: 41px; line-height: 1;
    color: var(--paper);
    white-space: nowrap;
  }

  .scan-frame {
    position: absolute; left: 858px; top: 12px;
    width: 214px; height: 222px;
    background: var(--paper);
    padding: 6px;
    transform: rotate(2deg);
    box-shadow: 0 3px 8px rgba(0,0,0,.25);
  }
  .scan-frame__image {
    width: 100%; height: 100%;
    background: radial-gradient(ellipse at 50% 45%, var(--scan-warm) 0%, #8c3c1c 55%, var(--scan-dark) 100%);
  }
</style>
</head>
<body>
  <section class="billboard">
    <svg class="billboard__bands" width="1080" height="318" viewBox="0 0 1080 318" aria-hidden="true">
      <path d="M277 262 C 520 210, 800 180, 1080 168 L1080 318 L277 318 Z" fill="#d49a2b"/>
      <path d="M277 274 C 520 222, 800 192, 1080 180 L1080 318 L277 318 Z" fill="#2f4a40"/>
    </svg>

    <div class="portrait" role="img" aria-label="Portrait of the studio owner in green scrubs holding an ultrasound probe"></div>

    <span class="corner corner--top"></span>
    <span class="corner corner--bottom"></span>

    <h1 class="headline">ADVANCED IMAGING</h1>
    <p class="tagline">Unforgettable Moments</p>
    <p class="services">
      <span>4D Ultrasound</span><span>•</span><span>Early Gender</span><span>•</span><span>Pregnancy Confirmation</span>
    </p>

    <div class="studio-card">
      <span class="studio-card__name">4D Cradle Glimpse</span>
      <span class="studio-card__rule"></span>
      <span class="studio-card__line">PRENATAL ULTRASOUND STUDIO</span>
    </div>

    <div class="phone">
      <span class="phone__icon">
        <svg width="19" height="19" viewBox="0 0 24 24" aria-hidden="true">
          <path fill="#ffffff" d="M6.6 10.8a15.1 15.1 0 0 0 6.6 6.6l2.2-2.2a1 1 0 0 1 1-.25 11.4 11.4 0 0 0 3.6.57 1 1 0 0 1 1 1V20a1 1 0 0 1-1 1A17 17 0 0 1 3 4a1 1 0 0 1 1-1h3.5a1 1 0 0 1 1 1c0 1.25.2 2.46.57 3.6a1 1 0 0 1-.25 1z"/>
        </svg>
      </span>
      <span class="phone__number">850-471-5923</span>
    </div>

    <figure class="scan-frame">
      <div class="scan-frame__image" role="img" aria-label="Warm-toned 4D ultrasound image of twins"></div>
    </figure>
  </section>
</body>
</html>
```